Wordpress Theme for Medical Clinics

** Please view updated Sitemap2.pdf doc to clarify some confusion ***

This is a multiuser WordPress subscription site for medical clinics. Please see attachment for sitemap. Please do not include extra content like social media icons, search bars, or images. If you have questions, please ask for clarification.
The site contains the following pages and sub-pages:

1. Home
2. Our Clinic
2a. Our Clinic > Mission
2b. Our Clinic > Services
2c. Our Clinic > Clinic Policies
2d. Our Clinic > Schedules
3. Our Staff
3a. Our Staff > [Staff member page]
4. Resources
4a. Resources > Patient Health (index)
4b. Resources > Patient Health (index) > [post]
4c. Resources > Links
4d. Resources > Forms
5. Alerts
5a. Alerts > [Alert Page]
6. Contact Us

Includes the Following Pages, Subpages, and Content
1. Home
a. About Us
b. Our Staff
c. Bulletins
d. Accepting New Patients (shown as an alert widget)
e. Links
i. Physician Toolbox
ii. Book an Appointment
f. Clinic Policies
i. Show first 3 policies (e.g. Late Arrivals, Missed Appointments, Fees)
ii. Link to Clinic Policies page
g. Primary widget (displayed on all pages)
i. Hours of operation
ii. Contact Info
1. Tel
2. Fax
3. Email
4. Address
5. Get directions (link to Google Maps)
2. Our Clinic
a. Main Page
i. Clinic Name
ii. Overview
iii. Languages Spoken
iv. Secondary Navigation
1. Mission
2. Services
3. Clinic Policies
4. Schedules (see attachment)
b. Our Clinic > Mission
c. Our Clinic > Services
i. For each service include service TITLE and DESCRIPTION
d. Our Clinic > Clinic Policies
i. For each policy include policy TITLE and DESCRIPTION
ii. Include the following policies in mockup
1. Late arrivals
2. Missed appointments
3. Fees for missed appointments
4. Referrals and follow-ups
5. Services not covered by RDA
6. Information for LTF patients
7. Medical Legal Reports
e. Our Clinic > Schedules
3. Our Staff
a. Main Page
i. Display a list of staff members. Include NAME and DESIGNATION
b. Our Staff > [Staff Name]
i. Include NAME, PICTURE, DESIGNATION, and BIO
4. Resources
a. Resources > Patient Health
i. Main Page
1. Posts (ordered by date)
a. Title
b. Summary
2. Side Navigation
a. Post Categories
ii. Patient Health > [post title]
1. Title
2. Post Category
3. Date
4. Author
5. Summary
6. Body
b. Resources > Links
1. Secondary Navigation - Categories
a. Sample Categories:
i. Local Services
ii. RDA and Drug Coverage
iii. Mental Health Resources
2. Category page
a. Include the following links in the 'Local Services' category
i. Hypertension clinics
ii. Home Care services
iii. Vaccine Clinics
c. Resources > Forms
i. Display a table with form TITLE and CATEGORY
ii. Side Navigation
1. Form Categories
a. Use the following sample Categories
i. Referrals
ii. Insurance
iii. Intake
iv. Discharge
v. Waivers
5. Alerts
a. Main page
i. List of all Alert posts
1. Include post TITLE as a link to the post
ii. Side Navigation
1. Alerts Archive
a. shown as Month + Number of posts
iii. Alerts > [Alert page]
1. Include TITLE, DATE, AUTHOR, BODY
6. Contact Us
a. Map
b. Hours of operation
c. Address
d. Phone number
e. Fax number
e. Fax number
f. Map
g. Email

Design notes:
- fixed width
- responsive (need designs for mobile, tablet, and desktop)
- simple, dark font, white background
- use Font Awesome icons where needed
- user adds own logo

Target Market(s)

Medical Clinics

Industry/Entity Type

Medical

Number of Pages Required

5+ page

Font styles to use
Serif
Sans Serif

Requirements
Must have
• Please keep designs very simple.
• Examples:
• https://www.quolbin.com/install
• http://www.ventrohax.com/company/about-us
• http://brindlequota.org/
• http://www.trosk.com/
Should not have
• Minimal or no use of shadows and gradients

```html
<!DOCTYPE html>
<html lang="en">
<head>
<meta charset="utf-8">
<title>Clinic Site – Home</title>
<link href="https://fonts.googleapis.com/css2?family=Montserrat:wght@600;700&family=Open+Sans:wght@600&display=swap" rel="stylesheet">
<style>
:root{
  --blue:#0a2aa6;
  --blue-dark:#0b2594;
  --sky:#5aa4dc;
  --gold:#c99a22;
  --gold-dark:#9c7516;
  --band:#4a4a4a;
  --ink:#333;
  --muted:#666;
  --footer:#2c2c2c;
  --footer-bar:#1d1d1d;
  --line:#ddd;
}
*{margin:0;padding:0;box-sizing:border-box}
html,body{width:821px;height:1200px;overflow:hidden}
body{position:relative;background:#f6f6f6;font-family:Arial,Helvetica,sans-serif;color:var(--ink)}
.abs{position:absolute}
ul{list-style:none}
a{color:inherit;text-decoration:none}

/* header */
.site-header{left:0;top:0;width:821px;height:88px;background:#fff}
.brand{left:79px;top:22px;font-family:'Montserrat',sans-serif;font-weight:700;font-size:25px;color:#333;letter-spacing:.3px}
.header-contact{right:73px;top:5px;text-align:right;font-size:10px;line-height:13.6px;color:#444}
.header-contact .mail{color:var(--gold)}
.main-nav{left:273px;top:54px;display:flex;font-size:10.4px;color:#333}
.main-nav a{height:24px;line-height:28px}
.main-nav .active{background:var(--blue);color:#fff;padding:0 9px;width:45px}
.nav-item{position:absolute;top:0}

/* hero */
.hero-band{left:0;top:88px;width:821px;height:252px;background:var(--band)}
.hero{left:69px;top:78px;width:684px;height:284px;background:var(--gold)}
.hero-photo{left:75px;top:83px;width:513px;height:275px;background:linear-gradient(120deg,#d6f1f7 0%,#9fd3e2 45%,#e8f7fa 100%)}
.hero-corner{left:715px;top:78px}
.hero-text{left:588px;top:136px;width:157px;text-align:center;font-family:'Open Sans',sans-serif;font-weight:600;font-size:16.5px;line-height:20.5px;color:#fff}
.hero-btn{left:612px;top:264px;width:117px;height:33px;background:#3b3b3b;border:2px solid #222;border-radius:5px;color:#fff;font-family:'Open Sans',sans-serif;font-weight:600;font-size:13px;line-height:29px;text-align:center}
.hero-dots{left:601px;top:346px;display:flex;gap:4px}
.hero-dots span{width:24px;height:3px;background:#8a6812}
.hero-dots .on{background:#fff}

/* section headings */
.heading{font-family:'Montserrat',sans-serif;font-weight:700;color:var(--blue);font-size:16.5px}
.heading.sky{color:var(--sky)}

/* about */
.about-photo{left:70px;top:402px;width:189px;height:135px;border:4px solid #fff;outline:1px solid #e2e2e2;background:linear-gradient(90deg,#cfc8bf 0%,#efece8 50%,#f7f7f5 100%)}
.about-text{left:273px;top:401px;width:234px;font-size:9.7px;line-height:13.7px;color:var(--muted);text-align:justify}
.about-text p+p{margin-top:13.7px}

/* staff / links */
.lists-box{left:69px;top:561px;width:438px;height:158px;border:1px solid var(--line);background:#f8f8f8}
.lists-divider{left:287px;top:566px;width:1px;height:148px;background:var(--line)}
.arrow-list li{position:relative;padding-left:10px;font-size:10px;color:#777;height:20.5px}
.arrow-list li::before{content:"";position:absolute;left:0;top:3px;border-left:3.5px solid var(--sky);border-top:3px solid transparent;border-bottom:3px solid transparent}
.btn-view{height:17px;line-height:17px;padding:0 4px;font-size:10px;color:#fff;background:var(--blue)}
.btn-view.sky{background:var(--sky)}

/* hours widget */
.hours{left:531px;top:393px;width:222px;height:287px;background:var(--blue);color:#fff}
.hours .title{position:absolute;left:12px;top:11px;font-family:'Open Sans',sans-serif;font-weight:600;font-size:16.5px}
.hours table{position:absolute;border-collapse:collapse;font-size:10px}
.hours td{height:16.4px;vertical-align:top}
.u{text-decoration:underline}

.new-patients{left:532px;top:695px;width:222px;height:51px;background:var(--gold);border-bottom:3px solid var(--gold-dark);color:#fff}
.new-patients h3{position:absolute;left:10px;top:8px;font-family:'Open Sans',sans-serif;font-weight:600;font-size:16px}
.new-patients p{position:absolute;left:11px;top:30px;font-size:10px}

/* alerts */
.alert h4{font-size:11.5px;font-weight:700;color:var(--blue);margin-bottom:6px;padding-left:2px}
.alert p{font-size:9px;line-height:13.6px;color:#333}
.alert .more{font-size:9px;color:var(--gold);margin-top:0}
.divider-v{left:520px;top:785px;width:1px;height:158px;background:var(--line)}

/* footer */
.site-footer{left:0;top:979px;width:821px;height:185px;background:var(--footer);color:#fff}
.footer-bar{left:0;top:1164px;width:821px;height:36px;background:var(--footer-bar);color:#fff;font-size:10px;line-height:36px;padding-left:73px}
.f-title{font-family:'Montserrat',sans-serif;font-weight:600;font-size:16px;color:#fff}
.f-list li{position:relative;padding-left:13px;font-size:10px;height:16.4px}
.f-list li::before{content:"";position:absolute;left:4px;top:3px;border-left:3.5px solid #fff;border-top:3px solid transparent;border-bottom:3px solid transparent}
.f-hours{font-size:10px;border-collapse:collapse}
.f-hours td{height:16.4px}
.f-contact{font-size:10px;line-height:11px}
</style>
</head>
<body>

<header class="abs site-header">
  <div class="abs brand">CLINIC SITE</div>
  <div class="abs header-contact">
    <div class="mail">info@velmorclinic.com</div>
    <div>Eastvale, NY 10411</div>
    <div>877-555-0142</div>
  </div>
  <nav class="abs main-nav" style="width:480px;height:24px">
    <a class="nav-item active" style="left:0">HOME</a>
    <a class="nav-item" style="left:76px">OUR CLINIC</a>
    <a class="nav-item" style="left:171px">STAFF</a>
    <a class="nav-item" style="left:240px">RESOURCES</a>
    <a class="nav-item" style="left:340px">ALERTS</a>
    <a class="nav-item" style="left:416px">CONTACT US</a>
  </nav>
</header>

<section>
  <div class="abs hero-band"></div>
  <div class="abs hero"></div>
  <svg class="abs hero-corner" width="40" height="45" viewBox="0 0 40 45" aria-hidden="true">
    <polygon points="0,0 40,0 40,45" fill="var(--band)"/>
  </svg>
  <div class="abs hero-photo" role="img" aria-label="Photo of a surgeon in a mask and cap in a bright hospital corridor with staff behind"></div>
  <div class="abs hero-text">Lorem Ipsum is simply dummy text of the printing and typesetting</div>
  <a class="abs hero-btn">Learn More</a>
  <div class="abs hero-dots"><span></span><span class="on"></span><span></span><span></span><span></span></div>
</section>

<section>
  <h2 class="abs heading" style="left:71px;top:374px">OUR CLINIC</h2>
  <div class="abs about-photo" role="img" aria-label="Photo of a doctor in a white coat writing on a clipboard"></div>
  <div class="abs about-text">
    <p>Lorem Ipsum is simply dummy text of the printing and typesetting industry. Lorem Ipsum has been the industry's standard dummy text ever since the 1500s, when an unknown printer took a galley of type and scrambled it to make.</p>
    <p>It has survived not only five centuries, but also the leap into electronic typesetting, remaining essentially unchanged. It was popularised in the 1960.</p>
  </div>
</section>

<section>
  <div class="abs lists-box"></div>
  <div class="abs lists-divider"></div>
  <h2 class="abs heading" style="left:96px;top:570px">STAFF</h2>
  <ul class="abs arrow-list" style="left:97px;top:602px">
    <li>Dr john Smith MD</li><li>Dr jane doe MD</li><li>Dr Bruce Almghty MD</li><li>Dr jhon Smith MD</li>
  </ul>
  <a class="abs btn-view" style="left:99px;top:690px">View All »</a>
  <h2 class="abs heading" style="left:327px;top:570px">LINKS</h2>
  <ul class="abs arrow-list" style="left:328px;top:607px">
    <li>Radiology Clinics</li><li>Physotherapy Clinics</li><li>LTF Clinics</li><li>KVRC Clinics</li>
  </ul>
  <a class="abs btn-view" style="left:330px;top:690px">View All »</a>
</section>

<aside class="abs hours">
  <div class="title">Hours Of Opration</div>
  <table style="left:20px;top:41px">
    <tr><td style="width:91px">Monday</td><td>8:00 AM - 6:00 PM</td></tr>
    <tr><td>Tusday</td><td>8:00 AM - 6:00 PM</td></tr>
    <tr><td>Wednesday</td><td>8:00 AM - 6:00 PM</td></tr>
    <tr><td>Thursday</td><td>8:00 AM - 6:00 PM</td></tr>
    <tr><td>Friday</td><td>8:00 AM - 6:00 PM</td></tr>
    <tr><td>Sataraday</td><td>8:00 AM - 4:00 PM</td></tr>
    <tr><td>Sunday</td><td>8:00 AM - 4:00 PM</td></tr>
    <tr><td class="u">Holiday hours</td><td></td></tr>
  </table>
  <div class="abs" style="left:20px;top:180px;font-size:10px">CONTACT INFO</div>
  <table style="left:18px;top:200px">
    <tr><td style="width:110px">Telephone</td><td>6045550187</td></tr>
    <tr><td>Email</td><td>contact@velmorclinic.com</td></tr>
    <tr><td>Address</td><td style="line-height:11px">48 Alder Street<br>Velmor B.C<br>Canada V2K4RT</td></tr>
  </table>
</aside>

<div class="abs new-patients">
  <h3>New Patients</h3>
  <p>Accepting New Patients &nbsp;<span class="u">Contact US</span></p>
</div>

<section>
  <h2 class="abs heading" style="left:77px;top:766px">ALERTS</h2>
  <article class="abs alert" style="left:71px;top:798px;width:437px">
    <h4>Alert Headline 1</h4>
    <p>Lorem ipsum dolor sit amet, consectetuer a iscing elit. Aenean commodo ligula eget dolo. Aenean massa. Cum sociis natoque penatibet Lorem ipsum dolor sit amet, consectetuer a iscing elit. Aenean commodo ligula eget dolo. Aenean massa. Cum sociis natoque penatibet</p>
    <p class="more">Read more...</p>
  </article>
  <article class="abs alert" style="left:73px;top:885px;width:437px">
    <h4>Alert Headline 2</h4>
    <p>Lorem ipsum dolor sit amet, consectetuer a iscing elit. Aenean commodo ligula eget dolo. Aenean massa. Cum sociis natoque penatibet Lorem ipsum dolor sit amet, consectetuer a iscing elit. Aenean commodo ligula eget dolo. Aenean massa. Cum sociis natoque penatibet</p>
    <p class="more">Read more...</p>
  </article>
  <div class="abs divider-v"></div>
  <h2 class="abs heading sky" style="left:540px;top:778px">Clinic Polices</h2>
  <ul class="abs arrow-list" style="left:542px;top:805px">
    <li style="height:16.4px">Late Arrivals</li>
    <li style="height:16.4px">Missed Appointments</li>
    <li style="height:16.4px">Fees for Missed Appointment</li>
    <li style="height:16.4px">Referrals and follow ups</li>
    <li style="height:16.4px">Services not covered by RDA</li>
    <li style="height:16.4px">Information for LTF Patients</li>
    <li style="height:16.4px">Medicial Legal Reports</li>
  </ul>
  <a class="abs btn-view sky" style="left:543px;top:927px">View All »</a>
</section>

<footer class="abs site-footer">
  <h3 class="abs f-title" style="left:78px;top:13px">Our Clinic</h3>
  <ul class="abs f-list" style="left:78px;top:41px">
    <li>Mission</li><li>Services</li><li>Schdules</li><li>Polices</li><li>Staff</li><li>Alerts</li><li>Contact us</li>
  </ul>
  <h3 class="abs f-title" style="left:209px;top:13px">Resources</h3>
  <ul class="abs f-list" style="left:209px;top:42px">
    <li>Our &nbsp;Clinic</li><li>Mission</li><li>Services</li>
  </ul>
  <h3 class="abs f-title" style="left:352px;top:12px">Hours Of Oprations</h3>
  <table class="abs f-hours" style="left:353px;top:41px">
    <tr><td style="width:91px">Monday</td><td>8:00 AM - 6:00 PM</td></tr>
    <tr><td>Tusday</td><td>8:00 AM - 6:00 PM</td></tr>
    <tr><td>Wednesday</td><td>8:00 AM - 6:00 PM</td></tr>
    <tr><td>Thursday</td><td>8:00 AM - 6:00 PM</td></tr>
    <tr><td>Friday</td><td>8:00 AM - 6:00 PM</td></tr>
    <tr><td>Sataraday</td><td>8:00 AM - 4:00 PM</td></tr>
    <tr><td>Sunday</td><td>8:00 AM - 4:00 PM</td></tr>
    <tr><td class="u">Holiday hours</td><td></td></tr>
  </table>
  <h3 class="abs f-title" style="left:595px;top:13px">Contact us</h3>
  <svg class="abs" style="left:601px;top:49px" width="14" height="14" viewBox="0 0 24 24" aria-hidden="true">
    <path fill="#fff" d="M6.6 10.8a15 15 0 0 0 6.6 6.6l2.2-2.2a1 1 0 0 1 1-.25 11.4 11.4 0 0 0 3.6.57 1 1 0 0 1 1 1V20a1 1 0 0 1-1 1A17 17 0 0 1 3 4a1 1 0 0 1 1-1h3.5a1 1 0 0 1 1 1c0 1.25.2 2.45.57 3.57a1 1 0 0 1-.25 1z"/>
  </svg>
  <div class="abs f-contact" style="left:628px;top:49px">6045550187</div>
  <svg class="abs" style="left:600px;top:74px" width="18" height="13" viewBox="0 0 18 13" aria-hidden="true">
    <rect x="0.7" y="0.7" width="16.6" height="11.6" fill="none" stroke="#fff" stroke-width="1.4"/>
    <path d="M1 1l8 6.5L17 1M1 12l6-5M17 12l-6-5" fill="none" stroke="#fff" stroke-width="1.3"/>
  </svg>
  <div class="abs f-contact" style="left:628px;top:74px">contact@velmorclinic.com</div>
  <svg class="abs" style="left:603px;top:100px" width="14" height="20" viewBox="0 0 14 20" aria-hidden="true">
    <path fill="#fff" d="M7 0a7 7 0 0 0-7 7c0 5 7 13 7 13s7-8 7-13a7 7 0 0 0-7-7zm0 9.8A2.8 2.8 0 1 1 7 4.2a2.8 2.8 0 0 1 0 5.6z"/>
  </svg>
  <div class="abs f-contact" style="left:628px;top:99px">48 Alder Street<br>Velmor B.C<br>Canada V2K4RT</div>
</footer>
<div class="abs footer-bar">Copyright © 2015 Helmstead Care and District Group. All Rights Reserved Terms of Use &nbsp;| &nbsp;Privacy Policy &nbsp;| &nbsp;Sitemap</div>

</body>
</html>
```